Business card design for a dynamic IT consulting company

We need a business card design for a young firm, specialized in the Telecommunications/Consulting industry. The name of the company is Quindor and Partners Business Consulting Ltd. (Short name: Quindor and Partnes)
Quindor = solve read reverse, so we aim to be uncomplicated and solution-oriented. The small pipe in our logo is also related to the word solve. So we need a new business card design, which is simple, eye catching and something non traditional (I would probably prefer a square shaped design rather than a rectangle, but open for suggestions). Attached our logo.

Target Market(s)

Usually our customers are Tier1 Telecoms providers (Q-Netra, Palorix, etc) and their executives.

Industry/Entity Type

Business

Contact Information for Business Card

Name: Bence Tolnavari
Email: b.tolnavari@quindor.hu
Web: www.quindor.hu
Mobile: +36 30 518 2769
Title: Managing Director

Optional:
Company name: Quindor and Partners Ltd.
Address: 1087 Budapest, Tolvenka str. 28/C, Hungary

Font styles to use
Other font styles liked:
• helveticaneue_medium, Prime Regular are used now.

Colors

Designer to choose colors to be used in the design.

Requirements
Must have
• I would like to have a 2 sided design.
Nice to have
• I thought if we make the logo a bit bigger (without the company name), that could go to the back with the company name below. I though, if the pipe in the logo is somehow touchable on the business card, would be nice and unique.

```html
<!DOCTYPE html>
<html lang="en">
<head>
<meta charset="utf-8">
<title>Quindor and Partners – Business Card</title>
<link rel="stylesheet" href="https://fonts.googleapis.com/css2?family=Open+Sans:wght@400;600;700&display=swap">
<style>
  :root {
    --backdrop: #e9e7e6;
    --card-frost: #f6f3f2;
    --card-band: #5c5e60;
    --brand-grey: #56585a;
    --brand-accent: #c2479a;
    --text-light: #ffffff;
    --text-soft: #e4e4e4;
    --rule: #d8d8d8;
  }
  * { margin: 0; padding: 0; box-sizing: border-box; }
  html, body {
    width: 1200px; height: 900px; overflow: hidden;
    background: var(--backdrop);
    font-family: "Open Sans", Arial, sans-serif;
  }
  .canvas { position: relative; width: 1200px; height: 900px; }

  .card {
    position: absolute;
    width: 556px; height: 342px;
    background: var(--card-frost);
    box-shadow: 0 6px 18px rgba(0,0,0,0.12);
    overflow: hidden;
  }
  .card--front { left: 238px; top: 62px; }
  .card--back  { left: 458px; top: 518px; width: 560px; }

  .card__brand {
    position: absolute; left: 0; right: 0; top: 0; height: 186px;
    display: flex; align-items: center; justify-content: center; gap: 16px;
  }
  .card--back .card__brand { opacity: 0.75; }
  .brand-square { width: 22px; height: 22px; background: var(--brand-accent); }
  .brand-name {
    font-size: 44px; font-weight: 400; color: var(--brand-grey);
    letter-spacing: 0.5px; white-space: nowrap;
  }

  .card__band {
    position: absolute; left: 0; right: 0; bottom: 0; height: 156px;
    background: var(--card-band);
    border-top: 1px solid rgba(0,0,0,0.15);
  }

  .holder { position: absolute; left: 74px; top: 56px; color: var(--text-light); }
  .holder__name { font-size: 17px; font-weight: 700; line-height: 22px; }
  .holder__title { font-size: 14.5px; font-weight: 400; line-height: 20px; color: var(--text-soft); }

  .contact-rule {
    position: absolute; left: 274px; top: 58px; width: 1px; height: 60px;
    background: var(--rule);
  }
  .contacts {
    position: absolute; left: 288px; top: 56px; list-style: none;
    color: var(--text-light); font-size: 14px; line-height: 19.5px;
  }
  .contacts li { display: flex; align-items: center; gap: 8px; }
  .contacts svg { width: 12px; height: 12px; fill: var(--text-light); flex: none; }

  .company-address {
    position: absolute; left: 0; right: 0; top: 52px; text-align: center;
    color: var(--text-soft); font-size: 16px; line-height: 23px;
  }
</style>
</head>
<body>
<div class="canvas">

  <section class="card card--front" aria-label="Card front">
    <div class="card__brand">
      <span class="brand-square"></span>
      <span class="brand-name">Quindor &amp; Partners</span>
    </div>
    <div class="card__band">
      <div class="holder">
        <p class="holder__name">Bence Tolnavari</p>
        <p class="holder__title">Managing Director</p>
      </div>
      <div class="contact-rule"></div>
      <ul class="contacts">
        <li>
          <svg viewBox="0 0 12 12" aria-hidden="true"><path d="M3 0h6a1 1 0 0 1 1 1v10a1 1 0 0 1-1 1H3a1 1 0 0 1-1-1V1a1 1 0 0 1 1-1zm0.6 1.4v7.8h4.8V1.4zM6 9.8a.7.7 0 1 0 0 1.4a.7.7 0 0 0 0-1.4z"/></svg>
          <span>+36 30 518 2769</span>
        </li>
        <li>
          <svg viewBox="0 0 12 12" aria-hidden="true"><path d="M0 2h12v8H0zM1 3v.4l5 3.3 5-3.3V3zm0 1.6V9h10V4.6L6 7.9z"/></svg>
          <span>b.tolnavari@quindor.hu</span>
        </li>
        <li>
          <svg viewBox="0 0 12 12" aria-hidden="true"><path d="M6 0a6 6 0 1 0 0 12A6 6 0 0 0 6 0zm-1 2.2 1.6 1.4-.6 1.6 1.8.8.3 2-1.4 1.8-.9-1.8-1.7-.6.2-1.8-1.5-1z"/></svg>
          <span>www.quindor.hu</span>
        </li>
      </ul>
    </div>
  </section>

  <section class="card card--back" aria-label="Card back">
    <div class="card__brand">
      <span class="brand-square"></span>
      <span class="brand-name">Quindor &amp; Partners</span>
    </div>
    <div class="card__band">
      <p class="company-address">
        Quindor and Partners Ltd.<br>
        1087 Budapest, Tolvenka str. 28/C, Hungary
      </p>
    </div>
  </section>

</div>
</body>
</html>
```